Expedition Cruise Sales Website for the Polar Regions (Antarctica & Arctic)

This will be a website for selling cruises.
This site should have a homepage, a ship page, destinations, and itineraries.
I have created a file specifying each page, and it is attached.
Pages:
1. Home
2. Cruise Lines
- 2.1 Ships
3. Destinations
- 3.1 Region - 3.2 Country - 3.3 City
4. Itineraries
- 4.1 Itinerary
5. Blog / Travel Tips 6. About Us
7. Contact
Please take a look on the attached pdf
Target Market(s)
Expedition Travelers
Coding
Coded - Design and coding required
Number of Pages Required
5+ page
Font styles to use
Look and feel
Each slider illustrates characteristics of the customer's brand and the style your logo design should communicate.

```html
<!DOCTYPE html>
<html lang="en">
<head>
<meta charset="utf-8">
<title>Contact Us – Polarwake</title>
<link href="https://fonts.googleapis.com/css2?family=Poppins:wght@400;500;600&family=Inter:wght@400;500;600&family=Fraunces:ital,wght@0,600;1,700&display=swap" rel="stylesheet">
<style>
:root{
  --navy:#13234a;
  --blue:#3378bb;
  --footer:#24365f;
  --line:#dfe5ee;
  --ink:#1d2433;
  --muted:#8a93a3;
  --white:#fff;
  --chat:#3fbf4f;
}
*{box-sizing:border-box;margin:0;padding:0}
html,body{width:711px;height:1200px;overflow:hidden;background:var(--white)}
body{position:relative;font-family:Inter,sans-serif;color:var(--ink)}
.abs{position:absolute}
.hero{left:0;top:0;width:711px;height:185px;background:linear-gradient(100deg,#1f3a2e 0%,#3c5a55 35%,#3f6f85 60%,#2f7f95 100%)}
.hero::after{content:"";position:absolute;inset:0;background:linear-gradient(180deg,rgba(15,28,60,.75) 0%,rgba(20,40,80,.35) 60%,rgba(20,40,80,.2) 100%)}
.brand{font-family:Poppins,sans-serif;font-weight:600;color:var(--white);display:flex;align-items:center;gap:5px;z-index:2}
.brand .dot{width:12px;height:12px;border-radius:50%;background:var(--white)}
.nav{top:25px;left:224px;display:flex;z-index:2;font-family:Poppins,sans-serif;font-size:5.5px;color:var(--white)}
.nav span{margin-right:22px}
.nav .active{color:#6fa8e0}
.navphone{left:536px;top:24px;z-index:2;color:var(--white);font-family:Poppins,sans-serif;font-weight:600;font-size:7px;display:flex;align-items:center;gap:3px}
.book{left:607px;top:20px;width:59px;height:18px;background:var(--blue);color:var(--white);font-family:Poppins,sans-serif;font-weight:600;font-size:5.5px;display:flex;align-items:center;justify-content:center;z-index:2}
.hero-title{top:78px;width:711px;text-align:center;font-family:Poppins,sans-serif;font-weight:600;font-size:24px;color:var(--white);z-index:2}
.crumb{top:113px;width:711px;text-align:center;font-family:Poppins,sans-serif;font-size:6.5px;color:#dfe6f2;z-index:2}
.crumb b{color:var(--white);font-weight:600;margin-left:6px}
.crumb i{font-style:normal;margin:0 6px}
.info{top:185px;left:0;width:711px;height:89px;border-bottom:1px solid var(--line)}
.card{position:absolute;top:0;height:89px;border-left:1px solid var(--line)}
.card.last{border-right:1px solid var(--line)}
.card svg{position:absolute;top:29px}
.card h3{position:absolute;top:29px;font-family:Poppins,sans-serif;font-weight:400;font-size:11px;color:var(--ink)}
.card p{position:absolute;top:48px;font-size:7.2px;line-height:12px;color:#3b4454;white-space:nowrap}
.talk{top:303px;width:711px;text-align:center;font-family:Poppins,sans-serif;font-weight:500;font-size:13px;line-height:15px;color:var(--navy)}
.talk em{font-family:Fraunces,serif;font-weight:700;font-style:italic}
.field{border:1px solid #d7dce4;background:var(--white);font-size:5.5px;color:var(--muted);padding:6px 7px}
.send{left:326px;top:449px;width:59px;height:18px;background:var(--blue);color:var(--white);font-weight:600;font-size:6px;display:flex;align-items:center;justify-content:center}
.map{left:118px;top:497px;width:474px;height:167px;background:linear-gradient(90deg,#7fd0dc 0%,#dfeee0 12%,#e9ece0 45%,#d6ebdc 75%,#8fd3e0 100%)}
.deals{left:0;top:741px;width:711px;height:252px;background:var(--blue)}
.ship{left:418px;top:708px;width:230px;height:285px;background:linear-gradient(180deg,#e7e9ec 0%,#cdd2d8 45%,#4d5663 65%,#8c98a6 85%,#dfe5ea 100%)}
.deals-title{left:63px;top:795px;font-family:Poppins,sans-serif;font-weight:400;font-size:17px;line-height:20px;color:var(--white)}
.deals-title b{font-weight:600}
.deals-sub{left:63px;top:841px;width:225px;font-size:7px;line-height:9px;color:#eef3fa}
.nl{border:none;background:var(--white);font-size:5.5px;color:var(--ink);padding:6px 8px;height:18px;width:139px}
.submit{left:63px;top:927px;width:59px;height:18px;background:var(--navy);color:var(--white);font-weight:600;font-size:5.5px;display:flex;align-items:center;justify-content:center}
.footer{left:0;top:993px;width:711px;height:207px;background:linear-gradient(180deg,#24375f 0%,#2b4068 55%,#22365c 100%)}
.fbrand{left:63px;top:1039px;font-size:16px}
.fabout{left:63px;top:1073px;width:222px;font-size:5.9px;line-height:11px;color:#dfe6f2}
.fhead{font-family:Poppins,sans-serif;font-weight:500;font-size:8px;color:var(--white)}
.fitem{font-size:5.5px;color:#e4eaf4;display:flex;align-items:center;gap:4px}
.links{font-size:5.3px;line-height:11.2px;color:#e4eaf4}
.social{left:348px;top:1111px;display:flex;gap:4px}
.social span{width:18px;height:18px;border:1px solid #c9d3e3;border-radius:50%}
.rule{left:63px;top:1159px;width:585px;height:1px;background:rgba(255,255,255,.18)}
.copy{left:63px;top:1178px;font-size:5.6px;color:#e4eaf4}
.copy b{font-weight:600;color:var(--white)}
.chat-badge{left:626px;top:979px;width:66px;height:29px;background:var(--white);border-radius:2px;box-shadow:0 1px 4px rgba(0,0,0,.2);padding:4px 5px;font-size:4.5px;color:var(--ink);line-height:5.5px}
.chat-badge b{color:var(--blue);font-size:8px;font-weight:600}
.chat-dot{left:666px;top:969px;width:21px;height:21px;border-radius:50%;background:var(--chat);border:2px solid var(--white)}
.totop{left:667px;top:1152px}
</style>
</head>
<body>
<div class="abs hero" role="img" aria-label="Coastal cliffs with stairs above a beach and turquoise sea"></div>
<div class="abs brand" style="left:38px;top:20px;font-size:16px"><span class="dot"></span>Polarwake</div>
<nav class="abs nav"><span>Home</span><span>Cruise lines</span><span>Destinations</span><span>Itineraries</span><span>Blog</span><span>About us</span><span class="active">Contact</span></nav>
<div class="abs navphone"><svg width="6" height="6" viewBox="0 0 24 24"><path d="M6 2l4 4-2 3c1 3 4 6 7 7l3-2 4 4-3 4C10 21 3 14 2 5z" fill="#fff"/></svg>555.019.2468</div>
<div class="abs book">Book Now!</div>
<h1 class="abs hero-title">Contact Us</h1>
<div class="abs crumb">Home<i>&gt;&gt;</i><b>Contact Us</b></div>

<section class="abs info">
  <div class="card" style="left:37px;width:168px">
    <svg style="left:25px" width="19" height="19" viewBox="0 0 24 24" fill="none" stroke="#3378bb" stroke-width="1.2"><path d="M6 3l4 4-2 3c1 3 4 6 7 7l3-2 4 4-3 4C10 22 2 14 2 6z"/><path d="M14 3a7 7 0 0 1 7 7M14 6a4 4 0 0 1 4 4"/></svg>
    <h3 style="left:52px">Phone</h3><p style="left:52px">+1 555-019-2468</p>
  </div>
  <div class="card" style="left:205px;width:150px">
    <svg style="left:22px" width="19" height="19" viewBox="0 0 24 24" fill="none" stroke="#3378bb" stroke-width="1.2"><path d="M4 5h16v11H9l-5 4z"/><path d="M8 9h8M8 12h5"/></svg>
    <h3 style="left:49px">Chat</h3><p style="left:49px">+1 555-019-2468</p>
  </div>
  <div class="card" style="left:355px;width:150px">
    <svg style="left:18px" width="19" height="19" viewBox="0 0 24 24" fill="none" stroke="#3378bb" stroke-width="1.2"><path d="M3 9l9-6 9 6v12H3z"/><path d="M3 9l9 7 9-7M3 21l7-6M21 21l-7-6"/><path d="M7 11V5h10v6M9 7h6M9 9h6"/></svg>
    <h3 style="left:45px">Email</h3><p style="left:45px">hello@polarwake.example</p>
  </div>
  <div class="card last" style="left:505px;width:168px">
    <svg style="left:18px" width="19" height="19" viewBox="0 0 24 24" fill="none" stroke="#3378bb" stroke-width="1.2"><circle cx="12" cy="12" r="10"/><circle cx="12" cy="12" r="8"/><path d="M12 6v6l4 2"/></svg>
    <h3 style="left:45px">Office Time</h3><p style="left:45px">Mon - Fri: 7.00 - 22.00<br>Sat - Sun: 9.00 - 20.00</p>
  </div>
</section>

<h2 class="abs talk">We would love to talk about you<br><em>amazing deals</em></h2>
<div class="abs field" style="left:167px;top:353px;width:185px;height:18px">Name</div>
<div class="abs field" style="left:359px;top:353px;width:186px;height:18px">Phone</div>
<div class="abs field" style="left:167px;top:379px;width:185px;height:18px">Email...</div>
<div class="abs field" style="left:359px;top:379px;width:186px;height:18px">Subject</div>
<div class="abs field" style="left:167px;top:405px;width:378px;height:36px">Message...</div>
<div class="abs send">Send</div>

<div class="abs map" role="img" aria-label="Road map of the United States showing office location"></div>

<section class="abs deals"></section>
<div class="abs ship" role="img" aria-label="Expedition cruise ship among ice floes in polar waters"></div>
<h2 class="abs deals-title">Get cruise deals <b>directly<br>in your inbox</b></h2>
<p class="abs deals-sub">Subscribe now and set sail on a journey of endless adventure with our exclusive cruise newsletter</p>
<div class="abs nl" style="left:63px;top:875px">First Name</div>
<div class="abs nl" style="left:209px;top:875px">Last Name</div>
<div class="abs nl" style="left:63px;top:901px">Email Address...</div>
<div class="abs nl" style="left:209px;top:901px">Chat Number</div>
<div class="abs submit">Submit</div>

<footer class="abs footer" role="img" aria-label="Dark blue tinted view of an icy polar sea"></footer>
<div class="abs brand fbrand"><span class="dot"></span>Polarwake</div>
<p class="abs fabout">Lorem Ipsum is simply dummy text of the printing and typesetting industry. Lorem Ipsum has been the industry's standard dummy text ever since the 1500s, when an unknown printer took a galley of type and scrambled it to make a type specimen book.</p>
<div class="abs fhead" style="left:348px;top:1034px">Contct Us</div>
<div class="abs fitem" style="left:348px;top:1054px;font-size:6.5px"><svg width="6" height="6" viewBox="0 0 24 24"><path d="M6 2l4 4-2 3c1 3 4 6 7 7l3-2 4 4-3 4C10 21 3 14 2 5z" fill="#fff"/></svg>555.019.2468</div>
<div class="abs fitem" style="left:348px;top:1071px"><svg width="6" height="5" viewBox="0 0 24 20"><path d="M1 2h22v16H1z" fill="#fff"/><path d="M1 2l11 9 11-9" stroke="#24365f" stroke-width="2" fill="none"/></svg>help@polarwake.example</div>
<div class="abs fhead" style="left:348px;top:1092px">Follow us</div>
<div class="abs social"><span></span><span></span><span></span><span></span></div>
<div class="abs fhead" style="left:485px;top:1034px">Quick Links</div>
<div class="abs links" style="left:485px;top:1053px">Home<br>Cruise Lines<br>Destinations<br>Itineraries<br>Blog<br>About Us<br>Contact</div>
<div class="abs links" style="left:547px;top:1053px">FAQ<br>Privacy Policy<br>Terms and Conditions<br>Booking Confirmation</div>
<div class="abs rule"></div>
<p class="abs copy">© 2025 <b>Polarwake</b> All Rights Reserved</p>
<svg class="abs totop" width="12" height="12" viewBox="0 0 12 12"><path d="M6 0l5 12-5-3-5 3z" fill="#fff"/></svg>

<div class="abs chat-badge">Available<br><b>24/7</b> to Assist with<br>Any Questions</div>
<div class="abs chat-dot"></div>
</body>
</html>
```